Business Card Design Project

We are rebranding an existing automotive collision repair business. The business is called dent haven. I have attached logo but I'm not tied to that. I want to leave this wide open.

I want this card to say we are professional, competent, cutting edge. We are focused on customers and use a lot of the latest technology to make the customer experience different. We sign customers in on iPads. Paperwork I signed electronically and updates are sent via text, email, logging on a website or as they wish. I want this innovation and image to come through in our cards

Target Market(s)

60%. Women 40% men. Age 35-60

Industry/Entity Type

Automotive

Requirements
Must have
• The card must have name, title, phone,email, cell, web page

```html
<!DOCTYPE html>
<html lang="en">
<head>
<meta charset="utf-8">
<title>Dent Haven — Business Card</title>
<link rel="stylesheet" href="https://fonts.googleapis.com/css2?family=Roboto:wght@300;400;700&display=swap">
<style>
  :root {
    --page-bg: #ececec;
    --card-white: #ffffff;
    --card-black: #0b0b0b;
    --card-edge: #d6d6d6;
    --brand-green: #6cc04a;
    --text-light: #f2f2f2;
  }
  * { box-sizing: border-box; margin: 0; padding: 0; }
  html, body {
    width: 1200px;
    height: 800px;
    overflow: hidden;
    background: var(--page-bg);
    font-family: "Roboto", Arial, sans-serif;
  }
  .canvas {
    width: 1200px;
    height: 800px;
    display: flex;
    flex-direction: column;
    align-items: center;
    justify-content: center;
    gap: 44px;
  }
  .card {
    width: 580px;
    height: 331px;
    position: relative;
  }
  .card--front {
    background: var(--card-white);
    border: 2px solid var(--card-edge);
    display: flex;
    align-items: center;
    justify-content: center;
  }
  .wordmark {
    display: flex;
    align-items: center;
    gap: 12px;
  }
  .wordmark__dot {
    width: 18px;
    height: 18px;
    border-radius: 50%;
    background: var(--brand-green);
  }
  .wordmark__name {
    font-weight: 700;
    font-size: 44px;
    letter-spacing: -0.5px;
    color: var(--brand-green);
    text-transform: capitalize;
  }
  .card--back {
    background: var(--card-black);
    color: var(--text-light);
  }
  .holder {
    position: absolute;
    top: 24px;
    right: 30px;
    display: flex;
    align-items: baseline;
    gap: 8px;
  }
  .holder__name {
    font-weight: 300;
    font-size: 25px;
    color: var(--brand-green);
  }
  .holder__title {
    font-weight: 400;
    font-size: 14px;
    color: var(--text-light);
  }
  .contacts {
    position: absolute;
    left: 30px;
    bottom: 24px;
    list-style: none;
    display: flex;
    flex-direction: column;
    gap: 9px;
  }
  .contacts__item {
    display: flex;
    align-items: center;
    gap: 14px;
    font-weight: 300;
    font-size: 18px;
    line-height: 22px;
  }
  .contacts__icon {
    width: 20px;
    height: 20px;
    flex: none;
    fill: none;
    stroke: var(--brand-green);
    stroke-width: 1.6;
    stroke-linecap: round;
    stroke-linejoin: round;
  }
</style>
</head>
<body>
<main class="canvas">
  <section class="card card--front" aria-label="Card front">
    <div class="wordmark">
      <span class="wordmark__dot"></span>
      <span class="wordmark__name">Dent Haven</span>
    </div>
  </section>

  <section class="card card--back" aria-label="Card back">
    <div class="holder">
      <span class="holder__name">Mark Ellery</span>
      <span class="holder__title">Director</span>
    </div>
    <ul class="contacts">
      <li class="contacts__item">
        <svg class="contacts__icon" viewBox="0 0 20 20" aria-hidden="true">
          <rect x="2" y="4.5" width="16" height="11" rx="1"/>
          <path d="M2.5 5l7.5 6 7.5-6"/>
        </svg>
        <span>hello@denthaven.com</span>
      </li>
      <li class="contacts__item">
        <svg class="contacts__icon" viewBox="0 0 20 20" aria-hidden="true">
          <circle cx="10" cy="10" r="7.5"/>
          <ellipse cx="10" cy="10" rx="3.2" ry="7.5"/>
          <path d="M2.5 10h15M4 6h12M4 14h12"/>
        </svg>
        <span>www.denthaven.com</span>
      </li>
      <li class="contacts__item">
        <svg class="contacts__icon" viewBox="0 0 20 20" aria-hidden="true">
          <path d="M5 2.5l3 3.5-1.6 2.2c.9 2 2.5 3.6 4.5 4.5l2.2-1.6 3.5 3-1.6 2.4C9.5 16.5 3.5 10.5 2.5 4.1z"/>
        </svg>
        <span>+1 (800) 555-0142</span>
      </li>
      <li class="contacts__item">
        <svg class="contacts__icon" viewBox="0 0 20 20" aria-hidden="true">
          <rect x="5.5" y="2" width="9" height="16" rx="1.5"/>
          <path d="M5.5 14.5h9M9 16.3h2"/>
        </svg>
        <span>+1 (800) 555-0142</span>
      </li>
    </ul>
  </section>
</main>
</body>
</html>
```